Software Development Consulting Company Needs Business Card Design

We need a new business card design for our consultants at Kestrel Works (kestrelworks.example). We are a small firm that provides high-end software development and methodology consulting to medium to large enterprise IT organizations.

Our logo uses Futura for the font and we would like to stick with navy blue and canary yellow for the logo colors. Attached are normal and reversed versions of our logos in illustrator format.
Updates

Hi Everyone, Thank yo very much for your amazing design ideas. I have created a poll for this project and our employees will be voting on the design they wish to use. We will be making a decision this Wednesday (October 22nd). Thanks again, Dale Hartwick

Industry/Entity Type

Business

```html
<!DOCTYPE html>
<html lang="en">
<head>
<meta charset="utf-8">
<title>Kestrel Works Business Card</title>
<link href="https://fonts.googleapis.com/css2?family=Jost:wght@500&family=Open+Sans:wght@400;600&display=swap" rel="stylesheet">
<style>
  :root {
    --navy: #1d4a6e;
    --ink: #3a3a3c;
    --muted: #6a6b6e;
    --canary: #e3d21a;
    --paper: #ffffff;
    --backdrop: #eceef2;
    --rule: #b9bcc2;
  }
  html, body {
    margin: 0;
    padding: 0;
    width: 1200px;
    height: 980px;
    overflow: hidden;
    background: var(--backdrop);
  }
  .stage {
    position: relative;
    width: 1200px;
    height: 980px;
  }
  .card {
    position: absolute;
    left: 240px;
    width: 720px;
    height: 412px;
    border-radius: 34px;
    box-shadow: 0 10px 28px rgba(40, 50, 70, 0.18);
    overflow: hidden;
  }
  .card--front { top: 58px; background: var(--paper); }
  .card--back { top: 510px; background: var(--navy); }

  .wordmark {
    position: absolute;
    display: flex;
    align-items: center;
    gap: 12px;
    font-family: "Jost", "Futura", sans-serif;
    font-weight: 500;
    letter-spacing: 0.14em;
    text-transform: uppercase;
    white-space: nowrap;
  }
  .wordmark__dot {
    width: 20px;
    height: 20px;
    border-radius: 50%;
    flex: none;
  }
  .card--front .wordmark {
    left: 40px;
    top: 148px;
    font-size: 28px;
    color: var(--navy);
  }
  .card--front .wordmark__dot { background: var(--canary); }

  .divider {
    position: absolute;
    left: 392px;
    top: 70px;
    width: 2px;
    height: 272px;
    background: linear-gradient(to bottom, rgba(185,188,194,0), var(--rule) 40%, var(--rule) 70%, rgba(185,188,194,0));
  }

  .contact {
    position: absolute;
    left: 420px;
    top: 96px;
    font-family: "Open Sans", "Myriad Pro", sans-serif;
    color: var(--ink);
  }
  .contact__name {
    margin: 0;
    font-size: 26px;
    font-weight: 600;
    color: var(--navy);
    line-height: 1.1;
  }
  .contact__title {
    margin: 2px 0 18px;
    font-size: 17px;
    color: var(--muted);
  }
  .contact__list {
    list-style: none;
    margin: 0;
    padding: 0;
    font-size: 17px;
    line-height: 30px;
  }
  .contact__list li {
    display: flex;
    align-items: center;
    gap: 8px;
  }
  .contact__icon {
    width: 16px;
    height: 16px;
    flex: none;
  }

  .card--back .wordmark {
    left: 0;
    right: 0;
    top: 138px;
    justify-content: center;
    font-size: 44px;
    color: var(--paper);
  }
  .card--back .wordmark__dot { background: var(--paper); }
  .back__url {
    position: absolute;
    left: 0;
    right: 0;
    top: 262px;
    margin: 0;
    text-align: center;
    font-family: "Open Sans", "Myriad Pro", sans-serif;
    font-size: 21px;
    letter-spacing: 0.16em;
    color: var(--paper);
  }
</style>
</head>
<body>
<main class="stage">
  <section class="card card--front" aria-label="Business card front">
    <div class="wordmark"><span class="wordmark__dot"></span>Kestrel Works</div>
    <div class="divider"></div>
    <div class="contact">
      <p class="contact__name">Your Name</p>
      <p class="contact__title">Title</p>
      <ul class="contact__list">
        <li>
          <svg class="contact__icon" viewBox="0 0 16 16" aria-hidden="true"><circle cx="8" cy="8" r="7" fill="none" stroke="#1d4a6e" stroke-width="1.4"/><path d="M5.5 4.5c.6 3 2.4 5.4 5 7l1-1.3-1.6-1-.8.8c-1-.7-1.7-1.6-2.2-2.8l.9-.6-.8-1.8z" fill="#1d4a6e"/></svg>
          012-345-6789
        </li>
        <li>
          <svg class="contact__icon" viewBox="0 0 16 16" aria-hidden="true"><rect x="1.5" y="3.5" width="13" height="9" rx="1" fill="#1d4a6e"/><path d="M2 4l6 5 6-5" fill="none" stroke="#fff" stroke-width="1.2"/></svg>
          info@kestrelworks.example
        </li>
        <li>
          <svg class="contact__icon" viewBox="0 0 16 16" aria-hidden="true"><g fill="none" stroke="#1d4a6e" stroke-width="1.2"><circle cx="8" cy="8" r="6.5"/><ellipse cx="8" cy="8" rx="3" ry="6.5"/><path d="M1.5 8h13M2.5 4.8h11M2.5 11.2h11"/></g></svg>
          www.kestrelworks.example
        </li>
        <li class="contact__address">Riverton + Lakefield, IL</li>
      </ul>
    </div>
  </section>

  <section class="card card--back" aria-label="Business card back">
    <div class="wordmark"><span class="wordmark__dot"></span>Kestrel Works</div>
    <p class="back__url">www.kestrelworks.example</p>
  </section>
</main>
</body>
</html>
```